Glimmer Step Blog

Need a blog design. I am the first fashion dance blogger-very exciting! My first project will be reporting on Twirling Under Lanterns which premieres this Monday-St. Patrick's Day. I am looking for an exciting format to represent my new venture. I will be focusing on ballroom dance fashion-I like creativity and look for something with a cool color scheme, artistic, could be modern or really open for someone to interpret this concept in a creative way. The blog name is GlimStep.

Fashion

```html
<!DOCTYPE html>
<html lang="en">
<head>
<meta charset="utf-8">
<title>Glimmer Step Blog</title>
<link rel="stylesheet" href="https://fonts.googleapis.com/css2?family=Bodoni+Moda:wght@600;700&family=Open+Sans:ital,wght@0,400;0,600;1,400&display=swap">
<style>
:root{
  --brown-dark:#3a2a12;
  --brown:#836a45;
  --brown-menu:#7a6440;
  --accent:#8b6a3a;
  --ink:#1f1f1f;
  --text:#666;
  --muted:#999;
  --line:#e6e2da;
  --white:#fff;
}
*{box-sizing:border-box;margin:0;padding:0}
html,body{width:1200px;height:2353px;overflow:hidden;background:var(--white);font-family:"Open Sans",Arial,sans-serif;color:var(--text)}
.page{position:relative;width:1200px;height:2353px}

/* header */
.masthead{position:absolute;left:0;top:0;width:1200px;height:424px}
.hero-art{position:absolute;left:455px;top:0;width:628px;height:424px;z-index:1;background:radial-gradient(circle at 55% 72%,#d6d6d9 0,#ebebed 20%,#f8f8f8 42%,#fff 65%)}
.brand{position:absolute;left:186px;top:96px;z-index:2;font-family:"Bodoni Moda",Georgia,serif;font-weight:700;font-size:56px;letter-spacing:-1px;color:var(--brown-dark);line-height:1}
.tagline{position:absolute;left:186px;top:184px;z-index:2;width:360px;font-size:28px;line-height:36px;color:#777;font-weight:400;letter-spacing:-.3px}
.tagline .q{color:#c8c8c8;font-size:26px}
.tagline cite{display:block;text-align:right;font-size:17px;font-style:italic;color:#777;margin-top:18px;padding-right:30px;letter-spacing:0}

/* nav */
.nav{position:absolute;left:0;top:424px;width:1200px;height:50px;background:var(--brown-dark)}
.nav ul{list-style:none;position:absolute;left:186px;top:0;display:flex;height:50px}
.nav li{font-size:18px;color:#b9ab92;line-height:50px;padding:0 18px;border-right:1px solid #4d3b20}
.nav li:first-child{padding-left:0}
.nav li:last-child{border-right:0}
.nav li.active{color:var(--white)}
.social{position:absolute;right:187px;display:flex;gap:8px}
.nav .social{top:14px}
.social span{width:20px;height:20px;border-radius:50%;background:#9a8a70;display:block}
.submenu{position:absolute;left:289px;top:477px;z-index:10;width:122px;background:var(--brown-menu);border:1px solid #5b4a2c;box-shadow:0 2px 4px rgba(0,0,0,.25);list-style:none;padding:11px 0 11px 10px}
.submenu li{font-size:12px;color:var(--white);line-height:24px;white-space:nowrap}
.submenu li::before{content:"▪ ";font-size:9px}

/* posts */
.posts{position:absolute;left:187px;top:552px;width:536px}
.post{position:relative;height:353px}
.post:first-child{height:309px}
.post-body{display:flex;gap:12px;height:256px;border-bottom:1px solid #eee}
.post:first-child .post-body{height:212px}
.post-thumb{flex:0 0 273px;height:188px;padding:4px;border:1px solid #ddd;background:var(--white);box-shadow:0 1px 3px rgba(0,0,0,.1)}
.post-thumb div{width:100%;height:100%}
.post-text{flex:1}
.meta{font-size:10px;font-style:italic;color:var(--accent);height:26px;line-height:20px;border-bottom:1px solid #eee}
.meta .comments{margin-left:28px}
.post-title{font-size:24px;font-weight:400;color:var(--ink);line-height:30px;margin:8px 0 10px;letter-spacing:-.3px}
.excerpt{font-size:12px;line-height:15px;color:var(--text)}
.share{display:flex;align-items:center;height:44px;gap:4px;font-size:9px;color:#555}
.share .btn{border:1px solid #ccc;background:#f3f3f3;padding:1px 5px;border-radius:2px}
.share .count{border:1px solid #ccc;padding:1px 4px}
.share .gap{width:14px}
.full-story{margin-left:auto;font-size:12px;color:#555}
.divider{border-top:1px dashed #aaa;margin-top:8px}

/* sidebar */
.sidebar{position:absolute;left:773px;top:552px;width:239px}
.welcome{height:397px;background:var(--brown);padding:32px 27px 0;color:var(--white);border-radius:2px}
.welcome h2{font-family:"Bodoni Moda",Georgia,serif;font-weight:600;font-size:30px;line-height:39px;margin-bottom:18px}
.welcome p{font-size:13px;line-height:21px}
.widget{position:relative;border:1px solid var(--line);border-radius:3px;background:var(--white);margin-top:30px;box-shadow:0 1px 2px rgba(0,0,0,.04)}
.widget-title{font-size:21px;color:var(--accent);font-weight:400}
.feed{height:442px;padding:26px 18px 0}
.feed-head{display:flex;align-items:center;gap:10px;margin-left:6px;padding-bottom:20px;border-bottom:1px solid #eee}
.feed-head small{display:block;font-size:11px;color:var(--muted);margin-left:6px}
.feed-item{display:flex;gap:10px;margin-top:22px;font-size:11px;line-height:15px;color:var(--text)}
.avatar{flex:0 0 37px;height:37px;padding:2px;border:1px solid #ddd}
.avatar div{width:100%;height:100%}
.feed-item em{color:var(--accent);font-size:9.5px}
.fb{height:317px}
.fb-head{background:var(--brown);color:var(--white);font-size:16px;height:47px;line-height:47px;padding-left:24px}
.fb-body{padding:14px 22px 0}
.fb-page{display:flex;gap:12px;align-items:center;padding-bottom:10px;border-bottom:1px solid #eee}
.fb-mark{width:36px;height:36px;background:var(--brown-dark)}
.fb-page b{display:block;font-size:12px;color:#3b5998}
.fb-page span{font-size:9px;border:1px solid #ccc;padding:0 4px}
.fb-count{font-size:9px;color:#333;margin:8px 0}
.fb-grid{display:grid;grid-template-columns:repeat(4,40px);gap:8px 10px;font-size:8.5px;color:#333;text-align:center;padding-bottom:8px;border-bottom:1px solid #eee}
.fb-grid div{white-space:nowrap}
.fb-grid div div{width:40px;height:36px;margin-bottom:3px}
.fb-foot{font-size:9px;color:#333;margin-top:10px}
.recent{height:421px;padding:26px 26px 0}
.recent .widget-title{padding-bottom:16px;border-bottom:1px solid #eee}
.comment{margin-top:20px;font-size:10.5px;line-height:14px;color:var(--text);letter-spacing:-.1px}
.comment em{display:block;color:var(--accent);font-size:9.5px;margin-top:6px}
.read-all{position:absolute;right:26px;bottom:30px;font-size:13px;color:#555}

/* footer */
.footer{position:absolute;left:0;top:2301px;width:1200px;height:52px;background:var(--brown-dark);color:#ddd;font-size:11px}
.footer p{position:absolute;left:187px;top:19px}
.footer .social{top:16px}
</style>
</head>
<body>
<div class="page">
  <header class="masthead">
    <div class="hero-art" role="img" aria-label="Silver-legged dancer in heels standing over a mirrored disco ball"></div>
    <div class="brand">GlimStep</div>
    <p class="tagline"><span class="q">“</span>Move Your Body to the Beat of Fashion.<span class="q">”</span><cite>- Maren Holt</cite></p>
  </header>

  <nav class="nav">
    <ul>
      <li>Television</li>
      <li class="active">Interviews</li>
      <li>Hairpins to Hemlines</li>
    </ul>
    <div class="social"><span></span><span></span><span></span><span></span></div>
  </nav>
  <ul class="submenu">
    <li>Designers</li>
    <li>Dancers</li>
    <li>Dance Industry</li>
  </ul>

  <main class="posts">
    <article class="post">
      <div class="post-body">
        <div class="post-thumb"><div role="img" aria-label="Group of dancers posing in a bright studio" style="background:linear-gradient(135deg,#b9b2c4,#7a5a60 55%,#d7d2d6)"></div></div>
        <div class="post-text">
          <div class="meta">March 17, 2014, <span class="comments">💬 5 Comments</span></div>
          <h3 class="post-title">Dolor sit amet, consec tetur adipiscing elit.</h3>
          <p class="excerpt">Lorem ipsum dolor sit amet, consec tetur adipiscing elit. In fermentum dolor non augue pretium egestas. Donec tincidunt at congue ut, posuere sit amet est. Vivamus scelerisque pretium ...</p>
        </div>
      </div>
      <div class="share"><span class="btn">Like</span><span class="count">3k</span><span class="gap"></span><span class="btn">Chirp</span><span class="count">316</span><span class="full-story">Full Story →</span></div>
      <div class="divider"></div>
    </article>

    <article class="post">
      <div class="post-body">
        <div class="post-thumb"><div role="img" aria-label="Dance troupe performing on a dark stage" style="background:radial-gradient(circle at 50% 60%,#6a5a4a,#1a1410 70%)"></div></div>
        <div class="post-text">
          <div class="meta">March 17, 2014, <span class="comments">💬 5 Comments</span></div>
          <h3 class="post-title">Dolor sit amet, consec tetur adipiscing elit.</h3>
          <p class="excerpt">Lorem ipsum dolor sit amet, consectetur adipiscing elit. In fermentum dolor non augue pretium egestas. Donec sem eros, tincidunt at congue ut, posuere sit amet est. Vivamus scelerisque viverra odio sit amet laoreet. Ut nec neque non justo rutrum tempor lobortis eu ante. Aliquam sagittis, nibh quis commodo auctor</p>
        </div>
      </div>
      <div class="share"><span class="btn">Like</span><span class="count">3k</span><span class="gap"></span><span class="btn">Chirp</span><span class="count">316</span><span class="full-story">Full Story →</span></div>
      <div class="divider"></div>
    </article>

    <article class="post">
      <div class="post-body">
        <div class="post-thumb"><div role="img" aria-label="Dancers in flowing white gowns leaping" style="background:linear-gradient(135deg,#9aa0a4,#d8dadc 50%,#7d8488)"></div></div>
        <div class="post-text">
          <div class="meta">March 17, 2014, <span class="comments">💬 5 Comments</span></div>
          <h3 class="post-title">Dolor sit amet, consec tetur adipiscing elit.</h3>
          <p class="excerpt">Lorem ipsum dolor sit amet, consectetur adipiscing elit. In fermentum dolor non augue pretium egestas. Donec tincidunt at congue ut, posuere sit amet est. Vivamus scelerisque viverra odio sit amet laoreet. Ut nec neque non rutrum tempor lobortis eu ante. Aliquam sagittis, commodo auctor tempor lobortis eu ante.</p>
        </div>
      </div>
      <div class="share"><span class="btn">Like</span><span class="count">3k</span><span class="gap"></span><span class="btn">Chirp</span><span class="count">316</span><span class="full-story">Full Story →</span></div>
      <div class="divider"></div>
    </article>

    <article class="post">
      <div class="post-body">
        <div class="post-thumb"><div role="img" aria-label="Ballroom couple in red and black costumes" style="background:radial-gradient(circle at 45% 45%,#9a5040,#3a1818 55%,#120808)"></div></div>
        <div class="post-text">
          <div class="meta">March 17, 2014, <span class="comments">💬 5 Comments</span></div>
          <h3 class="post-title">Dolor sit amet, consec tetur adipiscing elit.</h3>
          <p class="excerpt">Lorem ipsum dolor sit amet, consectetur adipiscing elit. In fermentum dolor non augue pretium egestas. Donec tincidunt at congue ut, posuere sit amet est. Vivamus scelerisque viverra odio sit amet laoreet. Ut nec neque non rutrum tempor lobortis eu ante. Aliquam sagittis, commodo auctor tempor lobortis eu ante.</p>
        </div>
      </div>
      <div class="share"><span class="btn">Like</span><span class="count">3k</span><span class="gap"></span><span class="btn">Chirp</span><span class="count">316</span><span class="full-story">Full Story →</span></div>
      <div class="divider"></div>
    </article>

    <article class="post">
      <div class="post-body">
        <div class="post-thumb"><div role="img" aria-label="Ballroom couple dancing on a competition floor" style="background:linear-gradient(135deg,#555,#bbb 50%,#444)"></div></div>
        <div class="post-text">
          <div class="meta">March 17, 2014, <span class="comments">💬 5 Comments</span></div>
          <h3 class="post-title">Dolor sit amet, consec tetur adipiscing elit.</h3>
          <p class="excerpt">Lorem ipsum dolor sit amet, consectetur adipiscing elit. In fermentum dolor non augue pretium egestas. Donec tincidunt at congue ut, posuere sit amet est. Vivamus scelerisque viverra odio sit amet laoreet. Ut nec neque non rutrum tempor lobortis eu ante. Aliquam sagittis, commodo auctor tempor lobortis eu ante.</p>
        </div>
      </div>
      <div class="share"><span class="btn">Like</span><span class="count">3k</span><span class="gap"></span><span class="btn">Chirp</span><span class="count">316</span><span class="full-story">Full Story →</span></div>
    </article>
  </main>

  <aside class="sidebar">
    <section class="welcome">
      <h2>Welcome to GlimStep</h2>
      <p>Our European Collection of International Standard dresses are all designed and hand crafted by International Couture Dress Design Houses. This collection features one of a kind dresses with a unique International flare. They have been imported especially for you; please enjoy your journey!</p>
    </section>

    <section class="widget feed">
      <div class="feed-head">
        <svg width="44" height="32" viewBox="0 0 44 32" aria-hidden="true"><circle cx="22" cy="16" r="12" fill="#8b6a3a"/></svg>
        <div><div class="widget-title">Chirper Feed</div><small>Join the Conversation</small></div>
      </div>
      <div class="feed-item"><div class="avatar"><div role="img" aria-label="Reader avatar" style="background:#d9c7a8"></div></div><p>GlimStep, lorem dolor sit amet, elit dolor sit amet... http://glimstep.5fd6z<br><em>2 hour ago, favourite, retweet</em></p></div>
      <div class="feed-item"><div class="avatar"><div role="img" aria-label="Reader avatar" style="background:#4a3a3a"></div></div><p>GlimStep, lorem dolor sit amet, elit dolor sit amet... http://glimstep.5fd6z<br><em>2 hour ago, favourite, retweet</em></p></div>
      <div class="feed-item"><div class="avatar"><div role="img" aria-label="Reader avatar" style="background:#2a1e1a"></div></div><p>GlimStep, lorem dolor sit amet, elit dolor sit amet... http://glimstep.5fd6z<br><em>2 hour ago, favourite, retweet</em></p></div>
      <div class="feed-item"><div class="avatar"><div role="img" aria-label="Reader avatar" style="background:#7a2a20"></div></div><p>GlimStep, lorem dolor sit amet, elit dolor sit amet... http://glimstep.5fd6z<br><em>2 hour ago, favourite, retweet</em></p></div>
    </section>

    <section class="widget fb">
      <div class="fb-head">Find us on Circlebook</div>
      <div class="fb-body">
        <div class="fb-page"><div class="fb-mark"></div><div><b>GlimStep</b><span>Like</span></div></div>
        <p class="fb-count">207 people like GlimStep</p>
        <div class="fb-grid">
          <div><div role="img" aria-label="Follower avatar" style="background:#b0703a"></div>Pacifico</div>
          <div><div role="img" aria-label="Follower avatar" style="background:#6a6a30"></div>Buyers</div>
          <div><div role="img" aria-label="Follower avatar" style="background:#8a7a60"></div>Tom Reyes</div>
          <div><div role="img" aria-label="Follower avatar" style="background:#3a6a5a"></div>James</div>
          <div><div role="img" aria-label="Follower avatar" style="background:#7a2a20"></div>James</div>
          <div><div role="img" aria-label="Follower avatar" style="background:#3a5a50"></div>Tom Reyes</div>
          <div><div role="img" aria-label="Follower avatar" style="background:#c8a070"></div>Tom Reyes</div>
          <div><div role="img" aria-label="Follower avatar" style="background:#a07a6a"></div>Jolly</div>
        </div>
        <p class="fb-foot">Circlebook social Plugin</p>
      </div>
    </section>

    <section class="widget recent">
      <h3 class="widget-title">Recent Comments</h3>
      <div class="comment">Lorem ipsum testing tincidu dolor sit amet, elit dolor sitsitnt amet posuere fermentum dolor non augue..<em>👤 Maren Holt &nbsp; ◷ March 17, 2014</em></div>
      <div class="comment">Lorem ipsum testing tincidu dolor sit amet, elit dolor sitsitnt amet posuere fermentum dolor non augue..<em>👤 Maren Holt &nbsp; ◷ March 17, 2014</em></div>
      <div class="comment">Lorem ipsum testing tincidu dolor sit amet, elit dolor sitsitnt amet posuere fermentum dolor non augue..<em>👤 Maren Holt &nbsp; ◷ March 17, 2014</em></div>
      <p class="read-all">Read All →</p>
    </section>
  </aside>

  <footer class="footer">
    <p>All Right Reserved Copyright © 2014 - Terms and Conditions</p>
    <div class="social"><span></span><span></span><span></span><span></span></div>
  </footer>
</div>
</body>
</html>
```